BOLD & MINIMALIST DESIGN NEEDED

We want a very bold but minimalistic business card design that is impactful and utilizes both sides of the business card. Our current logo is included for your use.

We want bold fonts and good use of negative space. We don't want the logo to overpower the design.

Target Market(s)

Professionals who are building new commercial buildings.

Industry/Entity Type

Construction

Contact Information for Business Card

Name, Title, email, office phone, cell phone, website

Font styles to use
Serif
Sans Serif

Requirements
Must have
• Bold design!

```html
<!DOCTYPE html>
<html lang="en">
<head>
<meta charset="utf-8">
<title>Ridgeline Design + Build — Business Card</title>
<link rel="stylesheet" href="https://fonts.googleapis.com/css2?family=Arimo:wght@400;700&display=swap">
<style>
  :root {
    --stage: #1f1f1f;
    --card-white: #f4f4f4;
    --brand-green: #7dbd3f;
    --ink-dark: #222222;
    --ink-text: #333333;
    --white: #ffffff;
  }
  * { margin: 0; padding: 0; box-sizing: border-box; }
  html, body { width: 1200px; height: 1059px; overflow: hidden; }
  body {
    background: var(--stage);
    font-family: "Arimo", Arial, sans-serif;
    position: relative;
  }
  .card {
    position: absolute;
    border-radius: 18px;
    overflow: hidden;
  }
  .card-front {
    left: 257px; top: 89px; width: 687px; height: 390px;
    background: var(--card-white);
  }
  .card-back {
    left: 254px; top: 547px; width: 693px; height: 393px;
    background: var(--brand-green);
  }
  .wordmark {
    position: absolute;
    font-weight: 700;
    text-align: center;
    line-height: 1;
  }
  .wordmark-front {
    left: 400px; top: 150px; width: 250px;
    color: var(--ink-dark);
  }
  .wordmark-front .wordmark-name { font-size: 33px; letter-spacing: 0.5px; }
  .wordmark-front .wordmark-tag { font-size: 14px; letter-spacing: 6px; margin-top: 8px; }
  .wordmark-back {
    left: 0; top: 170px; width: 100%;
    color: var(--white);
  }
  .wordmark-back .wordmark-name { font-size: 52px; letter-spacing: 1px; }
  .wordmark-back .wordmark-tag { font-size: 22px; letter-spacing: 10px; margin-top: 12px; }
  .brand-square {
    display: block;
    margin: 0 auto 14px;
    background: currentColor;
  }
  .wordmark-front .brand-square { width: 22px; height: 22px; margin-bottom: 12px; }
  .wordmark-back .brand-square { width: 30px; height: 30px; margin-bottom: 20px; }

  .person { position: absolute; left: 39px; top: 203px; }
  .person-name {
    color: var(--brand-green);
    font-weight: 700;
    font-size: 26px;
    line-height: 1;
  }
  .person-title {
    color: var(--ink-text);
    font-size: 18px;
    margin-top: 4px;
  }
  .divider {
    position: absolute;
    left: 39px; top: 265px; width: 609px; height: 1px;
    background: var(--brand-green);
  }
  .contact-list {
    position: absolute; left: 37px; top: 280px;
    list-style: none;
  }
  .contact-item, .contact-web {
    display: flex; align-items: center; gap: 5px;
    color: var(--ink-text);
    font-size: 18px;
    height: 28px;
  }
  .contact-web { position: absolute; right: 39px; top: 336px; }
  .icon { width: 12px; height: 12px; fill: var(--brand-green); flex: none; }
  .footer-bar {
    position: absolute;
    left: 397px; bottom: 0; width: 251px; height: 10px;
    background: var(--ink-dark);
  }
</style>
</head>
<body>
  <section class="card card-front" aria-label="Card front">
    <div class="wordmark wordmark-front">
      <span class="brand-square"></span>
      <div class="wordmark-name">RIDGELINE</div>
      <div class="wordmark-tag">DESIGN + BUILD</div>
    </div>

    <div class="person">
      <div class="person-name">DANA WHITLOW</div>
      <div class="person-title">Owner/CEO</div>
    </div>

    <div class="divider"></div>

    <ul class="contact-list">
      <li class="contact-item">
        <svg class="icon" viewBox="0 0 12 12"><path d="M2.5 0.5 4.5 3 3.4 4.3a7 7 0 0 0 4.3 4.3L9 7.5l2.5 2-1.3 2C5 11.3 0.7 7 0.5 1.8z"/></svg>
        07 5550 1234
      </li>
      <li class="contact-item">
        <svg class="icon" viewBox="0 0 12 12"><path d="M3 0h6a1 1 0 0 1 1 1v10a1 1 0 0 1-1 1H3a1 1 0 0 1-1-1V1a1 1 0 0 1 1-1zm0.6 1.2v8h4.8v-8zM6 9.8a.7.7 0 1 0 0 1.4.7.7 0 0 0 0-1.4z"/></svg>
        0400 555 246
      </li>
      <li class="contact-item">
        <svg class="icon" viewBox="0 0 12 12"><path d="M0 2h12v8H0zM1 3v.3L6 7l5-3.7V3zm0 1.6V9h10V4.6L6 8.2z"/></svg>
        hello@ridgelinebuild.com
      </li>
    </ul>

    <div class="contact-web">
      <svg class="icon" viewBox="0 0 12 12"><circle cx="6" cy="6" r="6"/></svg>
      www.ridgelinebuild.com
    </div>

    <div class="footer-bar"></div>
  </section>

  <section class="card card-back" aria-label="Card back">
    <div class="wordmark wordmark-back">
      <span class="brand-square"></span>
      <div class="wordmark-name">RIDGELINE</div>
      <div class="wordmark-tag">DESIGN + BUILD</div>
    </div>
  </section>
</body>
</html>
```